International Petrochemical business needs a web design for Clearway Desk system

We need a web design for a "Clearway Desk" system for an international petrochemical company. The web site is used internally within the company. It is hosted by an internal department which provides government permit request service for other departments.

We would like to see designs of two pages using color light blue. (home page, internal page as attached).
Home Page:
1. Header has a background image and small animation. Header on home page can be taller than the header of the internal page.
2. Layout as attached.

Internal Page:
1. Header can use the same background image as the home page and can be shorter to utilize the page for content.
2. The blue icon behind every captions represent an icon. When user move mouse over this icon, it displays the caption in Thai language as a tooltip. This icon needs to be redesign.

The final design should communicate the followings:
- Excellent service provided system in terms of time and accurary
- Rapid growth of business via building petrochemical refinery plant
Updates

For Internal Page, the blue circle behind every captions represent an icon. When mouse over this icon, a tool tip showing the caption in Thai language is shown. Please also design this icon..

There are more feedbacks from customer as followed:

1. Banner should consists of 
    1.1 "Approved" stamp on paper
    1.2 An image of Garuda. It is used on every government documents in Thailand
    1.3 Image of petrochemical plant
2. Each menu item (Home, Permit, Search, etc) should have different colors. Drop down menu will use the same color as its parent menu item.
3. Overall tone of the web page should be light blue with background of the body the web page in white
4. "New Request" button should use green color with icon on it
5. Table header of each box in the body of the page should use dark blue background with text in white

Please kindly submit your revisions.
Thank you.

Industry/Entity Type

Business

Requirements
Must have
• 1. Design for 1024x768 screen resolution
2. Use light blue theme
3. Background of header where the company logo is must have white background

```html
<!DOCTYPE html>
<html lang="en">
<head>
<meta charset="utf-8">
<title>Clearway Desk – Home</title>
<link href="https://fonts.googleapis.com/css2?family=Open+Sans:wght@400;600;700&display=swap" rel="stylesheet">
<style>
:root{
  --sky-top:#0a7fb0;
  --sky:#00aeef;
  --accent:#1aa3e4;
  --ink:#333333;
  --ink-soft:#444444;
  --head-bg:#2e2e2e;
  --link:#1a5cb0;
  --rule:#d9d9d9;
  --paper:#ffffff;
  --tab-light:#f2f2f2;
  --tab-dark:#2b2b2b;
  --pager-dark:#3c4f6b;
  --alert-red:#e32b2b;
  --alert-amber:#f4c20d;
}
*{box-sizing:border-box;margin:0;padding:0}
html,body{width:1200px;height:776px;overflow:hidden}
body{
  font-family:"Open Sans",Arial,sans-serif;
  background:linear-gradient(180deg,var(--sky-top) 0,var(--sky) 90px,var(--sky) 100%);
  color:var(--ink);
  position:relative;
}
.page{
  position:absolute;left:96px;top:14px;width:1010px;height:770px;
  background:var(--paper);
  border-radius:6px 6px 0 0;
  overflow:hidden;
}
/* header */
.masthead{position:absolute;left:0;top:0;width:100%;height:130px;
  background:linear-gradient(180deg,#ffffff 0,#f4f4f4 60%,#e9e9e9 100%)}
.title-bar{position:absolute;left:300px;right:0;top:0;height:39px;background:#050505;
  clip-path:polygon(0 0,100% 0,100% 100%,38px 100%)}
.title-bar span{position:absolute;right:33px;top:5px;color:#fff;font-size:22px;font-weight:400;letter-spacing:.2px}
.brand{position:absolute;left:54px;top:28px;display:flex;align-items:center;gap:8px}
.brand-dot{width:34px;height:34px;border-radius:50%;background:var(--accent)}
.brand-name{color:var(--accent);font-weight:700;font-size:12px;line-height:14px;text-transform:uppercase}
.nav{position:absolute;left:22px;top:90px;height:40px;filter:drop-shadow(0 0 1px #bdbdbd)}
.nav a{position:absolute;top:0;height:40px;width:150px;text-align:center;line-height:42px;
  font-size:14px;font-weight:700;color:var(--ink);text-decoration:none;text-transform:uppercase;
  background:linear-gradient(180deg,#ffffff,var(--tab-light));
  clip-path:polygon(0 100%,22px 8%,30px 0,120px 0,128px 8%,150px 100%)}
.nav a.is-active{background:var(--tab-dark);color:#fff;z-index:5}
.search{position:absolute;left:773px;top:88px;width:211px;height:29px;border-radius:15px;
  border:1px solid #cfcfcf;background:#fff;box-shadow:inset 0 1px 3px rgba(0,0,0,.15)}
.search-btn{position:absolute;right:-1px;top:-1px;width:40px;height:29px;border-radius:15px;background:#2a2a2a;
  display:flex;align-items:center;justify-content:center}
/* banner */
.hero{position:absolute;left:0;top:130px;width:100%;height:202px;
  background:linear-gradient(180deg,#7e6aa6 0,#9a7fb7 30%,#59607a 62%,#25332c 82%,#111a16 100%)}
.hero-caption{position:absolute;left:0;bottom:0;width:100%;height:34px;background:rgba(0,0,0,.55);
  color:#fff;font-size:14px;line-height:34px;padding-left:28px}
.hero-caption b{font-weight:600}
.hero-dots{position:absolute;right:42px;top:11px;display:flex;gap:5px}
.hero-dots i{width:13px;height:13px;border-radius:50%;background:#fff}
.hero-dots i.on{background:var(--accent)}
/* content */
.content{position:absolute;left:0;top:332px;width:100%;bottom:0;
  background:linear-gradient(180deg,#e4e4e4 0,#ffffff 70px)}
.panel{position:absolute}
.panel h2{font-size:23px;font-weight:700;color:var(--ink);line-height:30px;margin-bottom:6px}
.panel h2 em{font-style:normal;color:var(--accent)}
table{border-collapse:collapse;width:100%;font-size:13px}
th{background:var(--head-bg);color:#fff;font-weight:600;text-align:left;height:32px;padding:0 6px;
  border-right:1px solid #fff}
th:last-child{border-right:0}
td{height:31px;padding:0 6px;border-bottom:1px solid var(--rule);color:var(--ink-soft);line-height:16px}
td a{color:var(--link)}
td.num{text-align:right;padding-right:44px}
td.center{text-align:center}
.flag{display:inline-block;width:11px;height:11px;border-radius:50%;margin-left:5px;vertical-align:-1px;
  border:1px solid rgba(0,0,0,.25)}
.flag.red{background:var(--alert-red)}.flag.amber{background:var(--alert-amber)}
.pager{display:flex;justify-content:center;gap:3px;padding:6px 0;border-bottom:1px solid var(--rule)}
.pager span{width:22px;height:24px;border:1px solid #c4c4c4;border-radius:3px;background:linear-gradient(#fafafa,#e2e2e2);
  font-size:14px;line-height:22px;text-align:center;color:#555}
.pager .arrow{width:26px;background:linear-gradient(#5d7292,var(--pager-dark));border-color:#33445c;
  display:flex;align-items:center;justify-content:center;border-radius:6px}
.panel-new{left:25px;top:14px;width:451px}
.panel-work{left:532px;top:14px;width:448px}
.panel-new .rows,.panel-work .rows{height:157px;overflow:hidden}
.panel-new .pager,.panel-work .pager{border-top:1px solid var(--rule)}
.panel-work .rows tr:last-child td{border-bottom:0}
.panel-expire{left:25px;top:260px;width:950px}
</style>
</head>
<body>
<div class="page">
  <header class="masthead">
    <div class="title-bar"><span>Clearway Desk</span></div>
    <div class="brand"><div class="brand-dot"></div><div class="brand-name">Northgate<br>Petrochemical</div></div>
    <nav class="nav">
      <a class="is-active" style="left:0">Home</a>
      <a style="left:130px;z-index:4">Permits</a>
      <a style="left:255px;z-index:3">Report</a>
      <a style="left:373px;z-index:2">Admin</a>
      <a style="left:490px;z-index:1">Help</a>
    </nav>
    <div class="search">
      <div class="search-btn">
        <svg width="14" height="14" viewBox="0 0 14 14"><circle cx="6" cy="6" r="4.3" fill="none" stroke="#fff" stroke-width="1.8"/><line x1="9.2" y1="9.2" x2="12.8" y2="12.8" stroke="#fff" stroke-width="2" stroke-linecap="round"/></svg>
      </div>
    </div>
  </header>

  <section class="hero" role="img" aria-label="Petrochemical plant lit up at dusk">
    <div class="hero-caption"><b>Northgate Petrochemicals</b> is simply dummy text of the printing and typesetting
      <div class="hero-dots"><i class="on"></i><i></i><i></i></div>
    </div>
  </section>

  <main class="content">
    <section class="panel panel-new">
      <h2><em>New</em> Requests</h2>
      <div class="rows">
        <table>
          <tr><th style="width:108px">Request No.</th><th style="width:149px">Requested Date</th><th>Branch</th></tr>
          <tr><td><a href="#">56-0003</a></td><td>20/4/2013</td><td>GC1</td></tr>
          <tr><td><a href="#">56-0004</a></td><td>20/4/2013</td><td>GC2</td></tr>
        </table>
      </div>
      <div class="pager">
        <span class="arrow"><svg width="8" height="10" viewBox="0 0 8 10"><path d="M6 1 2 5l4 4" fill="none" stroke="#fff" stroke-width="2"/></svg></span>
        <span>1</span><span>2</span><span>3</span><span>4</span>
        <span class="arrow"><svg width="8" height="10" viewBox="0 0 8 10"><path d="M2 1l4 4-4 4" fill="none" stroke="#fff" stroke-width="2"/></svg></span>
      </div>
    </section>

    <section class="panel panel-work">
      <h2><em>My Working</em> Requests</h2>
      <div class="rows">
        <table>
          <tr><th style="width:108px">Request No.</th><th style="width:119px">Requested Date</th><th>Status</th></tr>
          <tr><td><a href="#">55-0200</a></td><td>20/4/2013</td><td>Waiting for process</td></tr>
          <tr><td><a href="#">55-0210</a></td><td>20/4/2013</td><td>In progress</td></tr>
          <tr><td><a href="#">55-0300</a></td><td>20/4/2013</td><td>Incomplete document</td></tr>
          <tr><td><a href="#">55-0301</a></td><td>20/4/2013</td><td>Cancel requested</td></tr>
        </table>
      </div>
      <div class="pager">
        <span class="arrow"><svg width="8" height="10" viewBox="0 0 8 10"><path d="M6 1 2 5l4 4" fill="none" stroke="#fff" stroke-width="2"/></svg></span>
        <span>1</span><span>2</span><span>3</span><span>4</span>
        <span class="arrow"><svg width="8" height="10" viewBox="0 0 8 10"><path d="M2 1l4 4-4 4" fill="none" stroke="#fff" stroke-width="2"/></svg></span>
      </div>
    </section>

    <section class="panel panel-expire">
      <h2><em>Expiring</em> Permits</h2>
      <table>
        <tr><th style="width:119px">Permit No</th><th style="width:121px">Expire Date</th><th style="width:254px">Permit Name</th><th style="width:122px">Branch</th><th style="width:157px">Required Time (Day)</th><th>Required Time (Day)</th></tr>
        <tr><td><a href="#">AB56001</a></td><td>25/3/2013</td><td>Permit Name ###10</td><td>GC1</td><td class="num">30<span class="flag red"></span></td><td class="center">-40</td></tr>
        <tr><td><a href="#">BIO5502</a></td><td>24/3/2013</td><td>Permit Name ###20</td><td>GC2</td><td class="num">60<span class="flag amber"></span></td><td class="center">15</td></tr>
      </table>
      <div class="pager" style="padding-top:6px">
        <span class="arrow"><svg width="8" height="10" viewBox="0 0 8 10"><path d="M6 1 2 5l4 4" fill="none" stroke="#fff" stroke-width="2"/></svg></span>
        <span>1</span><span>2</span><span>3</span><span>4</span>
        <span class="arrow"><svg width="8" height="10" viewBox="0 0 8 10"><path d="M2 1l4 4-4 4" fill="none" stroke="#fff" stroke-width="2"/></svg></span>
      </div>
    </section>
  </main>
</div>
</body>
</html>
```